Business Card Design Project

Business Card
We are rebranding with a new logo
Industry/Entity Type
Business
Contact Information for Business Card
Dennis Morvale +61 487215963 dennis@quorv.com.au P.O. Box 872 Fernlow QLD 4309
Requirements
Must have
- Logo

```html
<!DOCTYPE html>
<html lang="en">
<head>
<meta charset="utf-8">
<title>Quorv International – Business Card</title>
<link rel="stylesheet" href="https://fonts.googleapis.com/css2?family=Roboto:wght@400;700&family=Roboto+Condensed:wght@700&display=swap">
<style>
  :root {
    --backdrop: #2a2a2b;
    --card-paper: #f3f3f3;
    --brand-blue: #1b86bd;
    --wave-light: #14a6dc;
    --wave-mid: #0b7fb2;
    --wave-dark: #0a5677;
    --accent-orange: #f08a24;
    --accent-orange-light: #f7a640;
    --text-light: #ffffff;
  }
  * { box-sizing: border-box; margin: 0; padding: 0; }
  html, body {
    width: 1200px; height: 960px; overflow: hidden;
    background: var(--backdrop);
  }
  .business-card {
    position: absolute;
    left: 223px; top: 265px;
    width: 754px; height: 430px;
    border-radius: 18px;
    background: var(--card-paper);
    overflow: hidden;
    box-shadow: 0 6px 14px rgba(0,0,0,0.45);
  }
  .card-waves {
    position: absolute; inset: 0;
    width: 754px; height: 430px;
  }
  .brand-name {
    position: absolute;
    left: 62px; top: 118px;
    color: var(--brand-blue);
    font-family: "Roboto", sans-serif;
    font-weight: 700;
    line-height: 1;
  }
  .brand-name .brand-word {
    display: block;
    font-size: 70px;
    letter-spacing: 1px;
  }
  .brand-name .brand-sub {
    display: block;
    margin-top: 12px;
    font-size: 21px;
    letter-spacing: 4.6px;
  }
  .contact-block {
    position: absolute;
    right: 50px; top: 212px;
    text-align: right;
    font-family: "Roboto", sans-serif;
    color: var(--text-light);
  }
  .contact-name {
    font-family: "Roboto Condensed", sans-serif;
    font-weight: 700;
    font-size: 25px;
    color: var(--accent-orange);
    margin-bottom: 14px;
  }
  .contact-address {
    font-size: 17px;
    line-height: 23px;
    margin-bottom: 13px;
  }
  .contact-line {
    display: flex;
    justify-content: flex-end;
    align-items: center;
    gap: 8px;
    font-size: 17px;
    line-height: 24px;
  }
  .contact-icon { width: 16px; height: 16px; flex: none; }
</style>
</head>
<body>
  <div class="business-card">
    <svg class="card-waves" viewBox="0 0 754 430" aria-hidden="true">
      <defs>
        <radialGradient id="waveFill" cx="330" cy="300" r="430" gradientUnits="userSpaceOnUse">
          <stop offset="0" stop-color="var(--wave-light)"/>
          <stop offset="0.55" stop-color="var(--wave-mid)"/>
          <stop offset="1" stop-color="var(--wave-dark)"/>
        </radialGradient>
        <linearGradient id="orangeFill" x1="0" y1="0" x2="1" y2="0">
          <stop offset="0" stop-color="var(--accent-orange)"/>
          <stop offset="1" stop-color="var(--accent-orange-light)"/>
        </linearGradient>
      </defs>
      <path class="wave-edge" fill="var(--wave-dark)" opacity="0.55"
        d="M0,356 C120,392 260,384 352,300 C446,212 470,96 596,80 C670,72 725,80 754,88 L754,430 L0,430 Z"/>
      <path class="orange-band" fill="url(#orangeFill)"
        d="M0,298 C90,340 220,352 356,288 C260,360 130,384 0,350 Z"/>
      <path class="band-divider" fill="none" stroke="#ffffff" stroke-width="2.5"
        d="M0,352 C130,386 262,364 356,290"/>
      <path class="blue-wave" fill="url(#waveFill)"
        d="M0,362 C120,398 268,388 362,302 C452,218 480,104 604,90 C676,82 728,90 754,98 L754,430 L0,430 Z"/>
    </svg>

    <div class="brand-name">
      <span class="brand-word">Quorv</span>
      <span class="brand-sub">INTERNATIONAL</span>
    </div>

    <div class="contact-block">
      <p class="contact-name">DENNIS MORVALE</p>
      <p class="contact-address">P.O. Box 872<br>Fernlow QLD 4309</p>
      <p class="contact-line">+61 487215963
        <svg class="contact-icon" viewBox="0 0 16 16" aria-hidden="true"><path fill="var(--accent-orange)" d="M3.6 1.2l2.3 2.6-1.3 1.9c.9 2 2.5 3.7 4.6 4.7l1.9-1.3 2.6 2.3-1.2 2.4C7 13.6 2.3 9 1.4 2.4z"/></svg>
      </p>
      <p class="contact-line">dennis@quorv.com.au
        <svg class="contact-icon" viewBox="0 0 16 16" aria-hidden="true"><rect x="1" y="3" width="14" height="10" rx="1" fill="var(--accent-orange)"/><path d="M1.5 3.8L8 9l6.5-5.2" fill="none" stroke="var(--wave-mid)" stroke-width="1.3"/></svg>
      </p>
      <p class="contact-line">www.quorv.com.au
        <svg class="contact-icon" viewBox="0 0 16 16" aria-hidden="true"><circle cx="8" cy="8" r="7" fill="var(--accent-orange)"/><path d="M8 1v14M1 8h14M3 4c3 1.5 7 1.5 10 0M3 12c3-1.5 7-1.5 10 0" fill="none" stroke="var(--wave-mid)" stroke-width="1"/></svg>
      </p>
    </div>
  </div>
</body>
</html>
```